Velvet Ladle Wishes Website Design; Cupcake Business with a unique and bespoke design element

We need a website design for a new bespoke and unique business making gourmet cupcakes - but MOST IMPORTANTLY we design and handmake cupcake wrappers and toppers specifically for each client's event. We are based in Sydney, Australia. The final resulting website should be elegant yet whimsical reflecting the notion of dreams and very elegant events eg weddings and very special parties.

We want to eventually have about 5 pages, HOWEVER, this project is specifically for the first page (ie Home page) and one other only. The final required pages are: a HOME page; ABOUT US page; PHOTO GALLERY page; FLAVOUR MENU & OTHER PRODUCTS page; CONTACT & INTERNET ENQUIRY page.

We expect the HOME page to be quite elaborate, perhaps including some animation. We will be providing the text content for all the other pages, and basically they will have the same background as the home page. We are looking for a clean design that runs across each page thus giving the website a continuity that pulls it all together. We would like our logo to be included on each page.

PLEASE NOTE: We will want multiple pages worked on in the handover phase but initially we want a very concise, consistent template to limit the amount of work to prospective designers.

While we are primarily looking for the design phase to be covered by this project, we would certainly appreciate coding to be included and will take that into consideration when choosing a winner.
Updates

Hi Designers

We have added some more information to our brief - please review it.

Thanks and happy designing

Hi Designers

Please note that we have increased our Prize money to $750.00.  We hope this encourages you to participate.

Thanks and regards
Velvet Ladle Wishes

Hi Designers

We've just posted some photos to help give you an idea of what we do.  Please note our attention to detail and precision in our work.

Thanks
Velvet Ladle Wishes

Hi Designers

Please Note:  What makes us different  to any other cupcake business is that we design cupcake wrappers and toppers, unique to our client's event whether it be a wedding, a birthday party or product launch.  We consult with our client to understand themes, colours, styles etc.  We then have our designs printed, next they are cut by a specialised computerised cutting machine,  We assemble everything by hand, and usually embellish the wrapper and topper with pearls, crystals, feathers, lace, ribbons or whatever else is appropriate for the event.  All work is totally bespoke, unique and individual.  No other cupcake supplier that we know of goes to these lengths to satisfy their client's dreams.

THE WRAPPER AND TOPPER IS OUR PRIMARY SELLING POINT. 

PLEASE NOTE:- We have uploaded a new photograph which we want to be used as the main photograph on the landing page.

We have removed all previous photographs of cupcakes (except for one that we can't get rid of).

We don't want a picture of a cupcake on the landing page we want the image _D7C3239.jpg to be used for that purpose.

We have also uploaded our logo in a number of file formats as we have had requests from you for these.

Hi designers

we have a crazy busy weekend on and won't be able to make any decisions re our competition until Monday  -  sorry to keep you in suspense, just a couple more days please!

regards
Pam

Target Market(s)

Primarily women - brides, new mothers (Christenings), Event Planners, who place an emphasis on the beauty of a product rather than the cost

Industry/Entity Type

Events

Requirements
Must have
• It must have our Logo (see attached upload) on each page (our logo is a butterfly atop a cupcake resting on a spoon and our motto is "Creating Delicious Works of Art". The colours used are pale pink, blue and chocolate brown and we'd expect these colours to be repeated in the final website.
The website must have a photo gallery which we can access and add to/change as our business grows.
We need a contact page which has an "internet enquiry form".
There should be a "Menu" page describing our cupcake flavours.
The Home page must have a party/event feel to it - definitely making an enquirer want to enter further into the site.
Nice to have
• Our logo is attached below in the "uploads". One idea that we have had is to use the butterfly in the logo but start it as a caterpillar crawling on the screen; as it spins it's cocoon the words "Sweet Dreams Little Caterpillar" would appear on screen; this would incorporate the "Dreams" in our Business Name; then our logo butterfly would hatch. This encapsulates the idea of taking something plain (caterpillar/cupcake) and creating something beautiful (butterfly/OUR cupcake).
However, we are open to other design ideas.
The colours we would like to have are pale pink, blue and chocolate brown in the design.

Some websites we really admire are: www.mirabellhart.com www.ribbonglitterloaf.com.au and www.greetingsoriel.com.au
These websites have a lightness and sense of fantasy to them. They do not convey a corporate image at all, rather they make you want to be at the party.
Should not have
• No "Corporate" style.

Most Important: We already have a website which we are not happy with - that is why we are going through this exercise to replace it. That means we DO NOT want anything along the lines of our current website. We are expecting some fresh ideas for our prize money.

```html
<!DOCTYPE html>
<html lang="en">
<head>
<meta charset="utf-8">
<title>Velvet Ladle Wishes – Home</title>
<link rel="stylesheet" href="https://fonts.googleapis.com/css2?family=Open+Sans:wght@400;700&family=Playfair+Display:wght@400&display=swap">
<style>
  :root {
    --header-pink: #fbdce2;
    --side-pink: #f4b3cb;
    --side-pink-light: #fbe0ea;
    --chocolate: #352026;
    --title-pink: #fbd3e3;
    --brand-blue: #0b77c4;
    --nav-text: #3a4756;
    --nav-face: #fbe1e6;
    --nav-edge: #f6c6d2;
    --logo-brown: #5a3a2c;
    --photo-warm: #e9c3a4;
    --photo-rose: #c9a0a8;
    --white: #ffffff;
  }
  * { box-sizing: border-box; margin: 0; padding: 0; }
  html, body { width: 1200px; height: 959px; overflow: hidden; }
  body {
    position: relative;
    font-family: "Open Sans", Verdana, sans-serif;
    background: linear-gradient(90deg, var(--side-pink) 0, var(--side-pink-light) 56px, var(--side-pink-light) 1139px, var(--side-pink) 1200px);
  }
  .site-header {
    position: absolute; left: 0; top: 0; width: 1200px; height: 252px;
    background: var(--header-pink);
  }
  .brand {
    position: absolute; left: 410px; top: 60px; width: 336px;
    text-align: center; color: var(--logo-brown);
  }
  .brand-mark {
    display: block; width: 60px; height: 60px; margin: 0 auto 14px;
    border-radius: 50%; background: var(--white);
  }
  .brand-name {
    font-family: "Playfair Display", Georgia, serif;
    font-size: 34px; font-weight: 400; line-height: 1.1;
  }
  .brand-motto { margin-top: 6px; font-size: 14px; color: var(--logo-brown); }
  .main-nav { position: absolute; left: 881px; top: 47px; }
  .main-nav a {
    position: absolute; left: 0; width: 220px; height: 37px;
    display: flex; align-items: center; justify-content: center;
    background: var(--nav-face);
    border: 2px solid var(--nav-edge); border-radius: 4px;
    color: var(--nav-text); font-weight: 700; font-size: 13.5px;
    letter-spacing: 1.3px; text-decoration: none;
  }
  .main-content {
    position: absolute; left: 56px; top: 252px; width: 1083px; height: 644px;
    background: var(--chocolate);
  }
  .hero-photo {
    position: absolute; left: 33px; top: 20px; width: 522px; height: 584px;
    background: linear-gradient(160deg, var(--photo-rose) 0%, var(--photo-warm) 55%, #f0d6c2 100%);
  }
  .slide-pager { position: absolute; left: 366px; top: 612px; display: flex; gap: 9px; }
  .slide-pager span {
    width: 26px; height: 21px; border: 2px solid var(--white);
    color: var(--white); font-weight: 700; font-size: 15px; line-height: 17px;
    text-align: center;
  }
  .title-panel {
    position: absolute; left: 576px; top: 21px; width: 468px; height: 67px;
    background: var(--title-pink); padding: 17px 0 0 66px;
  }
  .title-panel h1 {
    color: var(--brand-blue); font-size: 28px; font-weight: 700;
    letter-spacing: 1.5px; line-height: 1;
  }
  .title-panel p {
    color: var(--chocolate); font-size: 12.5px; font-weight: 700;
    letter-spacing: 0.8px; margin-top: 3px;
  }
  .intro {
    position: absolute; left: 588px; top: 130px; width: 468px;
    color: var(--white); font-size: 15px; letter-spacing: 0.6px;
    line-height: 23.4px;
  }
  .intro p + p { margin-top: 23.4px; }
  .site-footer {
    position: absolute; left: 0; top: 896px; width: 1200px; height: 63px;
    background: var(--brand-blue); border-top: 2px solid var(--white);
    color: var(--white); font-size: 14.5px;
  }
  .footer-links { position: absolute; left: 61px; top: 20px; word-spacing: 2px; }
  .footer-links a { color: var(--white); text-decoration: none; }
  .copyright { position: absolute; right: 60px; top: 20px; }
</style>
</head>
<body>
  <header class="site-header">
    <div class="brand">
      <span class="brand-mark"></span>
      <div class="brand-name">Velvet Ladle Wishes</div>
      <div class="brand-motto">Creating Delicious Works of Art</div>
    </div>
    <nav class="main-nav">
      <a href="#" style="top:0">ABOUT US</a>
      <a href="#" style="top:50px">FLAVOUR MENU</a>
      <a href="#" style="top:98px">PHOTO GALLERY</a>
      <a href="#" style="top:145px">INTERNET ENQUIRY</a>
    </nav>
  </header>

  <main class="main-content">
    <div class="hero-photo" role="img" aria-label="Photograph of decorated cupcakes with colourful icing and toppers"></div>
    <div class="slide-pager"><span>1</span><span>2</span><span>3</span><span>4</span><span>5</span></div>

    <div class="title-panel">
      <h1>VELVET LADLE WISHES</h1>
      <p>CREATING DELICIOUS WORKS OF ART</p>
    </div>

    <div class="intro">
      <p>Velvet Ladle Wishes is a gourmet cupcake service based in Larkfield, Sydney, specialising in artistic creations focusing heavily on design, colour, theme and most importantly taste!</p>
      <p>We handcraft the best cupcakes that you have ever tasted and they're beautiful too. Our cupcake toppers and wrappers are designed personally for your event making them a unique work of art that have the WOW factor. It's not just a cupcake - Velvet Ladle Wishes are indulgent, luxurious, chic and delicious.</p>
      <p>We are experts in selecting just the right colours and accents to match your colour palette, theme, or company logo. Everything we do is completely bespoke and we use colour/fabric swatches, floral arrangements, invitations or even just an idea to create a display at your event which will have your guests talking for weeks! We work with you every step of the way to make sure that your cupcakes will not only meet your requirements but exceed your expectations too.</p>
    </div>
  </main>

  <footer class="site-footer">
    <div class="footer-links"><a href="#">Products</a> &nbsp;/ <a href="#">Menu Gallery</a> &nbsp;/ &nbsp;<a href="#">FAQ &amp; Testimonails</a> <a href="#">Contact</a></div>
    <div class="copyright">© Copyright Velvet Ladle Wishes 2011</div>
  </footer>
</body>
</html>
```